Business card for law firm

Need business card for new law firm. Think confident, authoritative, conservative, but not stuffy or old-fashioned.

Contact Information for Business Card

Content for card - logo (uploaded), plus the following:

Paul Whitcombe (larger font)
Managing Partner (larger font, but not as large as name)
Level 9, 7 Ferris Lane
Sydney NSW 2000
Main Tel 02 9364 2710
Direct Tel 02 8472 3159
Email paul@qvlegal.com.au
www.qvlegal.com.au

Letterhead design should include logo plus:
Level 9, 7 Ferris Lane
Sydney NSW 2000
Tel 02 8472 3159
www.qvlegal.com.au

```html
<!DOCTYPE html>
<html lang="en">
<head>
<meta charset="utf-8">
<title>Quayvale Legal – Business Card</title>
<link rel="stylesheet" href="https://fonts.googleapis.com/css2?family=Cinzel:wght@400;600&family=Open+Sans:wght@400;600&display=swap">
<style>
  :root {
    --backdrop: #86532a;
    --navy: #0b1f5a;
    --paper: #ffffff;
    --ink: #111111;
    --on-navy: #ffffff;
    --rule-on-navy: rgba(255, 255, 255, 0.35);
  }
  html, body {
    margin: 0;
    padding: 0;
    width: 1200px;
    height: 900px;
    overflow: hidden;
    background: var(--backdrop);
  }
  .canvas {
    position: relative;
    width: 1200px;
    height: 900px;
  }
  .card {
    position: absolute;
    left: 330px;
    width: 556px;
    height: 344px;
    box-shadow: 3px 4px 6px rgba(0, 0, 0, 0.45);
  }
  .card--contact {
    top: 90px;
    background: var(--navy);
    color: var(--on-navy);
    text-align: center;
    font-family: "Open Sans", Arial, sans-serif;
  }
  .card--brand {
    top: 469px;
    width: 560px;
    background: var(--paper);
    color: var(--ink);
    text-align: center;
  }
  .holder {
    position: absolute;
    top: 69px;
    left: 0;
    right: 0;
  }
  .holder__name {
    margin: 0;
    font-family: "Cinzel", "Times New Roman", serif;
    font-weight: 600;
    font-size: 21px;
    line-height: 26px;
    letter-spacing: 0.3px;
  }
  .holder__role {
    margin: 0;
    font-size: 15.5px;
    line-height: 20px;
  }
  .rule {
    width: 126px;
    height: 1px;
    margin: 9px auto 8px;
    background: var(--rule-on-navy);
    border: 0;
  }
  .details {
    margin: 0;
    padding: 0;
    list-style: none;
    font-size: 15.5px;
    line-height: 20.5px;
  }
  .details b { font-weight: 600; }
  .details small { font-size: 13px; }
  .brand-square {
    position: absolute;
    left: 250px;
    top: 89px;
    width: 60px;
    height: 60px;
    background: var(--navy);
  }
  .brand-name {
    position: absolute;
    top: 198px;
    left: 0;
    right: 0;
    margin: 0;
    font-family: "Cinzel", "Times New Roman", serif;
    font-weight: 400;
    color: var(--ink);
  }
  .brand-name__main {
    display: block;
    font-size: 50px;
    line-height: 56px;
    letter-spacing: 1px;
  }
  .brand-name__sub {
    display: block;
    font-size: 21px;
    line-height: 28px;
    letter-spacing: 13px;
    padding-left: 13px;
  }
</style>
</head>
<body>
<main class="canvas">
  <section class="card card--contact" aria-label="Card back – contact details">
    <div class="holder">
      <h1 class="holder__name">PAUL WHITCOMBE</h1>
      <p class="holder__role">Managing Partner</p>
      <hr class="rule">
      <ul class="details">
        <li><b>P:</b> 02 9364 2710</li>
        <li><b>P:</b> 02 8472 3159 <small>(DIRECT)</small></li>
        <li><b>E:</b> paul@qvlegal.com.au</li>
        <li>www.qvlegal.com.au</li>
      </ul>
      <hr class="rule">
      <ul class="details">
        <li>Level 9, 7 Ferris Lane</li>
        <li>Sydney NSW 2000</li>
      </ul>
    </div>
  </section>

  <section class="card card--brand" aria-label="Card front – firm name">
    <div class="brand-square" aria-hidden="true"></div>
    <h2 class="brand-name">
      <span class="brand-name__main">QUAYVALE</span>
      <span class="brand-name__sub">LEGAL</span>
    </h2>
  </section>
</main>
</body>
</html>
```